Magazine advertisement for wedding proposal

SPECS
Page size: 221,0-290,0
File format:Certified PDF PrintSpecs_7K2 (CMYK).
supply with crop marks on sheet mirror format
boundlessly knitted

CONTENT
I am going to ask my wife to marry me (again). I have bought a 1/1 page in her favourite Glossy. I would like the advertisement to present a letter from a type machine covered with some polaroid pictures of her. Idea is to mimic a guy in love writing a letter and dreaming away at her pictures. I would like the whole look and feel to be professional and in style. As such colours etc. may be changed and altered to make it a great integrated piece. I have added multiple pohoto's. Not all have to be used. You can choose which and how much you find most appealing. I At least want Photo Noor 1 to be used and one of the pictures with us together in white (couple).

The letter should read the following text:

Once in your lifetime you meet someone who changes everything.
She is going to do her thing with or without you. That's why she is a queen.

But we are just better together, babe...☺
That's why I want you to love me, stay with me and marry me. Would you?

Fenna,

Wil je met me trouwen?

-xxx-

Maurits

Requirements
Must have
• Be creative! This is just my first thought, but if you have an idea which you think is better, please let me know.
• - light & warm colours which all have the same look and feel (I do not like too much accent and opposite colours)
• - text as a love letter or poem
• - usage of Photo Noor 1
• - usage of couple photo
• - usage of both photo's with kids
Should not have
• - too cliché props - one or two things like hearts and flowers is ok, but dont overdo it

```html
<!DOCTYPE html>
<html lang="en">
<head>
<meta charset="utf-8">
<title>Wil je met me trouwen? – Magazine page</title>
<link href="https://fonts.googleapis.com/css2?family=Dancing+Script:wght@600;700&family=Kaushan+Script&family=Special+Elite&display=swap" rel="stylesheet">
<style>
  :root {
    --backdrop: #eef3f6;
    --page-pink: #eaa6bb;
    --page-pink-light: #f3c9d6;
    --page-white: #fdf4f7;
    --frame: #ffffff;
    --ink: #2b1a1f;
    --proposal-red: #e3111b;
    --heart-red: #e8232c;
    --blossom-pink: #ee7fc4;
    --blossom-leaf: #c9c873;
    --photo-portrait-a: #c9b39a;
    --photo-portrait-b: #8fa6c8;
    --photo-couple-a: #a9c3db;
    --photo-couple-b: #d9c4b0;
  }
  * { box-sizing: border-box; margin: 0; padding: 0; }
  html, body {
    width: 1200px; height: 1200px; overflow: hidden;
    background: var(--backdrop);
  }
  .canvas { position: relative; width: 1200px; height: 1200px; }
  .ad-page {
    position: absolute; left: 217px; top: 20px;
    width: 765px; height: 1160px;
    background: linear-gradient(180deg, var(--page-pink) 0%, var(--page-pink) 62%, var(--page-pink-light) 85%, var(--page-white) 100%);
    overflow: hidden;
    box-shadow: 0 4px 18px rgba(0,0,0,0.12);
  }
  .polaroid {
    position: absolute; background: var(--frame); padding: 8px;
    border-radius: 3px;
    box-shadow: 0 2px 6px rgba(0,0,0,0.08);
  }
  .polaroid .photo { width: 100%; height: 100%; }
  .polaroid--portrait { left: 20px; top: 36px; width: 344px; height: 403px; }
  .polaroid--portrait .photo { background: linear-gradient(160deg, var(--photo-portrait-a) 0%, #e6cdb6 45%, var(--photo-portrait-b) 100%); }
  .polaroid--couple { left: 381px; top: 154px; width: 348px; height: 406px; }
  .polaroid--couple .photo { background: linear-gradient(180deg, var(--photo-couple-a) 0%, #c7d6e2 40%, var(--photo-couple-b) 100%); }
  .heart { position: absolute; left: 103px; top: 372px; width: 190px; height: 175px; }
  .blossom { position: absolute; }
  .blossom--top {
    left: 400px; top: 5px; width: 365px; height: 262px;
    background: radial-gradient(ellipse at 65% 30%, var(--blossom-pink) 0%, rgba(238,127,196,0.55) 30%, rgba(201,200,115,0.35) 55%, rgba(234,166,187,0) 75%);
  }
  .blossom--bottom {
    left: 0; top: 995px; width: 200px; height: 165px;
    background: radial-gradient(ellipse at 40% 60%, var(--blossom-pink) 0%, rgba(238,127,196,0.5) 35%, rgba(201,200,115,0.3) 58%, rgba(253,244,247,0) 78%);
  }
  .love-letter {
    position: absolute; left: 36px; top: 585px; width: 700px;
    font-family: "Special Elite", monospace;
    font-size: 22px; line-height: 36px; color: var(--ink);
  }
  .love-letter p + p { margin-top: 12px; }
  .love-letter .salutation { margin-top: 14px; }
  .proposal {
    position: absolute; left: 40px; top: 915px; width: 700px;
    font-family: "Kaushan Script", cursive; font-weight: 400;
    font-size: 66px; line-height: 1; color: var(--proposal-red);
    text-align: center; white-space: nowrap;
  }
  .closing {
    position: absolute; right: 38px; top: 1010px;
    text-align: right; color: var(--ink);
  }
  .closing .kisses {
    font-family: "Special Elite", monospace; font-size: 22px; line-height: 34px;
  }
  .closing .signature {
    font-family: "Dancing Script", cursive; font-weight: 700;
    font-size: 36px; line-height: 48px;
  }
</style>
</head>
<body>
<div class="canvas">
  <article class="ad-page">
    <div class="blossom blossom--top" role="img" aria-label="Watercolour pink flowers with green leaves"></div>

    <figure class="polaroid polaroid--portrait">
      <div class="photo" role="img" aria-label="Photo of a smiling blonde woman in an off-shoulder striped top at a street café"></div>
    </figure>

    <svg class="heart" viewBox="0 0 204 188" aria-hidden="true">
      <path d="M102 186 C60 150 4 110 4 58 C4 24 30 4 58 4 C80 4 96 18 102 34 C108 18 124 4 146 4 C174 4 200 24 200 58 C200 110 144 150 102 186 Z" fill="var(--heart-red)"/>
    </svg>

    <figure class="polaroid polaroid--couple">
      <div class="photo" role="img" aria-label="Photo of the couple dressed in white embracing against a blue sky"></div>
    </figure>

    <div class="blossom blossom--bottom" role="img" aria-label="Watercolour pink flowers with green leaves"></div>

    <div class="love-letter">
      <p>Once in your lifetime you meet someone who changes<br>
      everything.<br>
      She is going to do her thing with or without you.<br>
      That's why she is a queen.</p>
      <p>But we are just better together, babe...<br>
      That's why I want you to love me, stay with me and<br>
      marry me. Would you?</p>
      <p class="salutation">Fenna,</p>
    </div>

    <h1 class="proposal">Wil je met me trouwen?</h1>

    <div class="closing">
      <p class="kisses">-xxx-</p>
      <p class="signature">Maurits</p>
    </div>
  </article>
</div>
</body>
</html>
```